PLUMA Project Roll Up Banner 85x200 cm (1:10, 1200 dpi)

PLUMA is a EU-funded project to promote female entrepreneurship networks. The project is developed by 9 partners from 7 different countries.
The banner is to be used throughout the project in exhibitions, conferences, roundtables, etc.
It has to include the following graphic elements, which cannot be modified beyond scaling:
- PLUMA logo
- EU logo (cannot be modified in any way, and cannot have any kind of background, but pure white).
- 9 partners logos
- Facebook link (with logo)
- LinkedIn link (with logo)
- Project's website (www.pluma-circle.example)
The text to be included:
Pioneering Ladies Undertaking Market Advances
PLUMA: Contributes to the strengthening of the links between women entrepreneurs and the mainstream of new technologies, educational, and training practices offered all over Europe.
GOOD PRACTICES: Compilation of EU projects promoting female entrepreneurship and ICT systems for learning, supporting, and training women entrepreneurs.
NETWORK: Strengthening of linkages between EU women entrepreneurs, project managers, learning communities, multipliers, and society to encourage a knowledge-sharing environment through the creation of the PLUMA circle.
ONE-STOP SHOP: Development of a multi-lingual EU online platform, where valuable an innovative EU learning opportunities can be found and accessed at one single place, as well as fostering new business opportunities by a Virtual Market.
The banner has to be attractive the modern female entrepreneur. It has to be easy to read, and present a fresh and exciting identity.
The banner has to include 5 additional centimetres on the top, and 10 on the bottom.
The last partner logo has been uploaded now.
Female entrepreneurs
Higher Educational Institutions
Government Female Representatives
Environment

```html
<!DOCTYPE html>
<html lang="en">
<head>
<meta charset="utf-8">
<title>PLUMA Roll Up Banner</title>
<link rel="stylesheet" href="https://fonts.googleapis.com/css2?family=Tenor+Sans&family=Open+Sans:wght@400;700&display=swap">
<style>
  :root {
    --page: #ffffff;
    --paper: #ffffff;
    --frame: #c8ccd2;
    --band: #231f20;
    --band-text: #d9d9d9;
    --accent: #f6a52a;
    --body-text: #6d6e71;
    --label: #231f20;
    --brand: #5a5f86;
    --eu-blue: #1d3f9a;
    --programme: #2a5db0;
    --chip-social: #3b6db3;
    --chip-pro: #1a86c8;
  }
  * { box-sizing: border-box; margin: 0; padding: 0; }
  html, body { width: 1200px; height: 1000px; overflow: hidden; background: var(--page); }
  .banner {
    position: absolute; left: 412px; top: 58px;
    width: 376px; height: 885px;
    background: var(--paper);
    border: 1px solid var(--frame);
    display: flex; flex-direction: column;
  }
  .brand-row {
    flex: 0 0 153px; display: flex; align-items: center;
    justify-content: space-between; padding: 0 16px 0 26px;
  }
  .project-mark { display: flex; align-items: center; gap: 8px; }
  .project-mark .dot { width: 34px; height: 34px; border-radius: 50%; background: var(--brand); }
  .project-mark .name {
    font-family: "Tenor Sans", sans-serif; font-size: 30px;
    color: var(--brand); letter-spacing: 1px;
  }
  .programme { display: flex; align-items: center; gap: 8px; }
  .programme .flag { width: 66px; height: 46px; background: var(--eu-blue); }
  .programme .label {
    font-family: "Open Sans", sans-serif; font-size: 13px; line-height: 15px;
    color: var(--programme);
  }
  .tagline {
    flex: 0 0 100px; background: var(--band); color: var(--band-text);
    font-family: "Tenor Sans", sans-serif;
    display: flex; align-items: center; justify-content: center;
    text-align: center; padding: 0 28px; position: relative;
  }
  .tagline h1 { font-weight: 400; font-size: 19px; line-height: 24px; }
  .tagline .quote { font-size: 30px; line-height: 1; position: absolute; color: var(--band-text); font-family: "Open Sans", sans-serif; font-weight: 700; }
  .tagline .open { left: 10px; top: 14px; }
  .tagline .close { right: 10px; bottom: 16px; }
  .rule { flex: 0 0 10px; background: var(--accent); }
  .pillars {
    flex: 0 0 258px; padding: 18px 16px 0 16px;
    font-family: "Open Sans", sans-serif; font-size: 9.3px; line-height: 13.5px;
    color: var(--body-text);
  }
  .pillars p { margin-bottom: 10px; }
  .pillars b { color: var(--label); font-weight: 700; }
  .section-head {
    flex: 0 0 30px; background: var(--band); color: #ffffff;
    font-family: "Tenor Sans", sans-serif; font-size: 14px;
    display: flex; align-items: center; justify-content: center;
  }
  .partners {
    flex: 0 0 157px; display: grid;
    grid-template-columns: repeat(3, 1fr); grid-template-rows: repeat(3, 1fr);
    align-items: center; justify-items: center; padding: 6px 10px;
  }
  .badge { display: block; }
  .website {
    flex: 0 0 36px; background: var(--band); color: var(--band-text);
    font-family: "Tenor Sans", sans-serif; font-size: 20px;
    display: flex; align-items: center; justify-content: center;
  }
  .website-rule { flex: 0 0 6px; background: var(--accent); }
  .social {
    flex: 0 0 80px; background: var(--band); padding: 0 16px;
    display: flex; flex-direction: column; justify-content: center; gap: 10px;
  }
  .social-link {
    display: flex; align-items: center; gap: 14px;
    font-family: "Open Sans", sans-serif; font-weight: 700; font-size: 11.5px;
    color: #ffffff; white-space: nowrap;
  }
  .social-link .chip { flex: 0 0 24px; height: 24px; background: var(--chip-social); border-radius: 3px; }
  .social-link .chip.pro { background: var(--chip-pro); }
  .foot-margin { flex: 1; background: var(--paper); }
</style>
</head>
<body>
  <main class="banner">
    <header class="brand-row">
      <div class="project-mark">
        <span class="dot"></span>
        <span class="name">PLUMA</span>
      </div>
      <div class="programme">
        <span class="flag"></span>
        <span class="label">Continuing<br>Study<br>Programme</span>
      </div>
    </header>

    <section class="tagline">
      <span class="quote open">“</span>
      <h1>Pioneering Ladies Undertaking Market Advances.</h1>
      <span class="quote close">”</span>
    </section>
    <div class="rule"></div>

    <section class="pillars">
      <p><b>PLUMA:</b> Contributes to the strengthening of the links between women entrepreneurs and the mainstream of new technologies, educational, and training practices offered all over Europe.</p>
      <p><b>GOOD PRACTICES:</b> Compilation of EU projects promoting female entrepreneurship and ICT systems for learning, supporting, and training women entrepreneurs.</p>
      <p><b>NETWORK:</b> Strengthening of linkages between EU women entrepreneurs, project managers, learning communities, multipliers, and society to encourage a knowledge-sharing environment through the creation of the PLUMA circle.</p>
      <p><b>ONE-STOP SHOP:</b> Development of a multi-lingual EU online platform, where valuable an innovative EU learning opportunities can be found and accessed at one single place, as well as fostering new business opportunities by a Virtual Market.</p>
    </section>

    <div class="section-head">Partners</div>
    <section class="partners" aria-label="Partner organisations">
      <svg class="badge" width="92" height="30" role="img" aria-label="Partner badge"><rect width="92" height="30" rx="3" fill="#58b8c9"/></svg>
      <svg class="badge" width="92" height="30" role="img" aria-label="Partner badge"><rect width="92" height="30" rx="3" fill="#2f4f9a"/></svg>
      <svg class="badge" width="100" height="24" role="img" aria-label="Partner badge"><rect width="100" height="24" rx="3" fill="#3a3f4a"/></svg>
      <svg class="badge" width="96" height="30" role="img" aria-label="Partner badge"><rect width="96" height="30" rx="3" fill="#1f5fae"/></svg>
      <svg class="badge" width="70" height="30" role="img" aria-label="Partner badge"><rect width="70" height="30" rx="3" fill="#f08a1c"/></svg>
      <svg class="badge" width="112" height="30" role="img" aria-label="Partner badge"><rect x="1" y="1" width="110" height="28" fill="#ffffff" stroke="#d0312d" stroke-width="2"/></svg>
      <svg class="badge" width="52" height="40" role="img" aria-label="Partner badge"><rect width="52" height="40" rx="3" fill="#4f9a4a"/></svg>
      <svg class="badge" width="66" height="36" role="img" aria-label="Partner badge"><rect width="66" height="36" rx="3" fill="#6cbcb8"/></svg>
      <svg class="badge" width="110" height="40" role="img" aria-label="Partner badge"><rect width="110" height="40" rx="3" fill="#8fbf3a"/></svg>
    </section>

    <div class="website">www.pluma-circle.example</div>
    <div class="website-rule"></div>
    <section class="social">
      <div class="social-link"><span class="chip"></span>www.socialwall.example/pluma.circle</div>
      <div class="social-link"><span class="chip pro"></span>www.prolink.example/groups/PLUMA-4402719</div>
    </section>
    <div class="foot-margin"></div>
  </main>
</body>
</html>
```